Brindlewick Solutions Ltd

I'd like to create a company letterhead for the attached logo in word format.

I'd like to emphasis the icon in large translucent state from the left corner and ensure that the letterhead colouring matches the colour palette of the current logo with a contrast so it's clear to see. I've attached a copy of our sister company page on the app for reference.

```html
<!DOCTYPE html>
<html lang="en">
<head>
<meta charset="utf-8">
<title>Brindlewick Solutions Ltd — Letterhead</title>
<link rel="stylesheet" href="https://fonts.googleapis.com/css2?family=Arimo:wght@400&family=Mulish:wght@400;700;800&family=PT+Sans&display=swap">
<style>
  :root {
    --teal: #12bfa9;
    --ink: #555555;
    --ink-soft: #5e5e5e;
    --muted: #9a9a9a;
    --rule-grey: #a9aaa9;
    --paper: #ffffff;
    --backdrop: #e2e2e2;
  }
  * { margin: 0; padding: 0; box-sizing: border-box; }
  html, body { width: 1200px; height: 1200px; overflow: hidden; background: var(--backdrop); }
  .canvas { position: relative; width: 1200px; height: 1200px; }
  .letterhead {
    position: absolute; left: 233px; top: 81px;
    width: 734px; height: 1038px;
    background: var(--paper);
  }
  .brand {
    position: absolute; left: 65px; top: 42px;
    display: flex; align-items: center; gap: 12px;
  }
  .brand-dot { width: 52px; height: 52px; border-radius: 50%; background: var(--teal); }
  .brand-name {
    font-family: "Mulish", sans-serif; font-weight: 400;
    font-size: 29px; color: var(--teal); letter-spacing: -0.2px;
  }
  .salutation {
    position: absolute; left: 67px; top: 318px;
    font-family: "Mulish", sans-serif; font-weight: 800;
    font-size: 17px; color: var(--ink);
  }
  .body-copy {
    position: absolute; left: 65px; top: 366px; width: 602px;
    font-family: "Arimo", sans-serif; font-size: 12.4px;
    line-height: 15.1px; color: var(--ink-soft);
  }
  .body-copy p + p { margin-top: 13px; }
  .closing {
    position: absolute; left: 67px; top: 677px;
    font-family: "Mulish", sans-serif; font-weight: 700;
    font-size: 10px; color: var(--ink);
  }
  .signature {
    position: absolute; left: 84px; top: 726px;
    font-family: "PT Sans", sans-serif; font-size: 19px;
    letter-spacing: -1.2px; color: var(--ink);
  }
  .footer-rule { position: absolute; left: 0; top: 990px; width: 734px; height: 14px; }
  .footer-contacts {
    position: absolute; left: 0; top: 1008px; width: 734px;
    display: flex; justify-content: center; align-items: center; gap: 8px;
    font-family: "Arimo", sans-serif; font-size: 11.2px; color: var(--muted);
    padding-right: 20px;
  }
  .footer-contacts .divider { color: var(--teal); font-weight: 700; }
  .footer-contacts .item { display: inline-flex; align-items: center; gap: 7px; }
  .footer-contacts .item + .item { margin-left: 4px; }
  .footer-contacts svg { width: 10px; height: 10px; fill: var(--teal); }
</style>
</head>
<body>
<div class="canvas">
  <article class="letterhead">
    <header class="brand">
      <span class="brand-dot"></span>
      <span class="brand-name">Brindlewick Solutions Ltd</span>
    </header>

    <h1 class="salutation">Dear Mr. Halvorsen,</h1>

    <section class="body-copy">
      <p>Lorem ipsum dolor sit amet, consectetuer adipiscing elit, sed diam nonmmy nibh euismod tincidunt ut laor eet dolore magna aliquam erat volutpat. Ut wisi enim ad minim veniam, quis nostrud exerci tationmcorper suscipit lobortis nisl ut aliquip ex ea commodo consequat. Duis autem vel eum iriure dolor in hendrerit in vulputate velit esse molestie consequat, vel illum dolore eu feugiat</p>
      <p>Rorem ipsum dolor sit amet, consectetuer adipiscing elit, sed diam nonmmy nibh euismod tincidunt ut laor eet dolore magna aliquam erat volutpat. Ut wisi enim ad minim veniam, quis nostrud exerci tationmcorper suscipit lobortis nisl ut aliquip ex ea commodo consequat. Duis autem vel eum iriure dolor in hendrerit in vulputate velit esse molest</p>
      <p>Dorem ipsum dolor sit amet, consectetuer adipiscing elit, sed diam nonmmy nibh euismod tincidunt ut laor eet dolore magna aliquam erat volutpat. Ut wisi enim ad minim veniam, quis nostrud exerci tationmcorper suscipit lobortis nisl ut aliquip ex ea commodo consequat. Duis autem vel eum iriure dolor in hendrerit in suscipit lobortis nisl ut aliquip ex ea commodo consequat. Duis autem vel eum iriure dolor in hendrerit in vulputate velit esse molestie consequat, vel illum</p>
      <p>Sorem ipsum dolor sit amet, consectetuer adipiscing elit, sed diam nonmmy nibh euismod tincidunt ut laor eet dolore magna aliquam erat volutpat. Ut wisi enim ad minim veniam, quis nostrud exerci tationmcorper suscipit lobortis nisl ut aliquip ex ea commodo consequat. Duis autem vel eum iriure dolor in</p>
    </section>

    <p class="closing">Sincerely,</p>
    <p class="signature">Marten Olsby</p>

    <svg class="footer-rule" viewBox="0 0 734 14" aria-hidden="true">
      <rect x="0" y="2" width="658" height="4" fill="var(--teal)"/>
      <rect x="0" y="8" width="658" height="1.6" fill="var(--rule-grey)"/>
      <rect x="697" y="2" width="37" height="4" fill="var(--teal)"/>
      <rect x="697" y="8" width="37" height="1.6" fill="var(--rule-grey)"/>
      <circle cx="677" cy="4" r="14" fill="var(--teal)"/>
    </svg>

    <footer class="footer-contacts">
      <span class="item">Your address, city, state, ZIP 0000</span>
      <span class="divider">|</span>
      <span class="item">
        <svg viewBox="0 0 24 24"><path d="M6.6 10.8a15.1 15.1 0 0 0 6.6 6.6l2.2-2.2a1 1 0 0 1 1-.25 11.4 11.4 0 0 0 3.6.6 1 1 0 0 1 1 1V20a1 1 0 0 1-1 1A17 17 0 0 1 3 4a1 1 0 0 1 1-1h3.5a1 1 0 0 1 1 1c0 1.25.2 2.45.6 3.6a1 1 0 0 1-.25 1z"/></svg>
        123-456-2100
      </span>
      <span class="item">
        <svg viewBox="0 0 24 24"><path d="M2 5h20v14H2z M2 5l10 8 10-8" fill="var(--teal)"/><path d="M3 6l9 7 9-7" fill="none" stroke="#fff" stroke-width="1.6"/></svg>
        youremail@mailbox.com
      </span>
      <span class="item">
        <svg viewBox="0 0 24 24"><circle cx="12" cy="12" r="10"/><path d="M2 12h20M12 2c3 3 3 17 0 20M12 2c-3 3-3 17 0 20" fill="none" stroke="#fff" stroke-width="1.4"/></svg>
        www.yourwebsite.com
      </span>
    </footer>
  </article>
</div>
</body>
</html>
```